VOR Exterior Coatings

double sided. the front i want the name of the business each word on a new line with the VOR being bigger. id like teal, black and white colors. the back i want my contact info. Flat, no gloss. Something professional and I want to feel the letters bump put of the card. if possible maybe a paint sprayer in corner. not a car paint spray. (no tank on top of gun)
no vehicle paint sprayers. that means no tank on top of the gun. doesn't have to have a sprayer. black/dark background on the front. white back ground on back with info

```html
<!DOCTYPE html>
<html lang="en">
<head>
<meta charset="utf-8">
<title>VOR Exterior Coatings – Business Card</title>
<link href="https://fonts.googleapis.com/css2?family=Arimo:wght@400;700&display=swap" rel="stylesheet">
<style>
  :root {
    --teal: #00858a;
    --ink: #222326;
    --card-dark: #141415;
    --logo-grey: #8e8f91;
    --paper: #ffffff;
    --stage: #e4e4e4;
    --rule: #9a9a9a;
  }
  * { margin: 0; padding: 0; box-sizing: border-box; }
  html, body { width: 1200px; height: 1015px; overflow: hidden; }
  body {
    background: var(--stage);
    font-family: "Arimo", Arial, sans-serif;
    position: relative;
  }
  .card {
    position: absolute;
    left: 215px;
    width: 770px;
    height: 440px;
    overflow: hidden;
    box-shadow: 0 6px 18px rgba(0,0,0,0.18);
  }
  .card--front { top: 45px; background: var(--card-dark); }
  .card--back { top: 530px; background: var(--paper); }

  .wordmark {
    position: absolute;
    font-weight: 700;
    line-height: 0.95;
    text-transform: uppercase;
  }
  .wordmark span { display: block; }
  .wordmark .wordmark__main { font-size: 118px; letter-spacing: 6px; }
  .wordmark .wordmark__sub { font-size: 46px; letter-spacing: 3px; }

  .card--front .wordmark {
    color: var(--logo-grey);
    left: 0; right: 0; top: 95px;
    text-align: center;
  }

  .card--back .wordmark {
    color: var(--teal);
    left: 58px; top: 118px;
  }
  .card--back .wordmark .wordmark__main { font-size: 96px; letter-spacing: 4px; }
  .card--back .wordmark .wordmark__sub { font-size: 36px; letter-spacing: 2px; }

  .divider {
    position: absolute;
    left: 385px; top: 92px;
    width: 1px; height: 230px;
    background: var(--rule);
  }

  .contact {
    position: absolute;
    left: 418px; top: 82px;
    color: var(--ink);
  }
  .contact__name {
    color: var(--teal);
    font-weight: 700;
    font-size: 25px;
    letter-spacing: 0.5px;
  }
  .contact__title { font-size: 19px; margin-bottom: 14px; }
  .contact__line {
    display: flex; align-items: center; gap: 10px;
    font-size: 19px; height: 28px;
  }
  .contact__line svg { width: 18px; height: 18px; flex: none; }
  .contact__address { font-size: 19px; line-height: 1.3; margin-top: 12px; padding-left: 28px; }

  .band { position: absolute; bottom: 0; }
  .band--teal { left: 0; width: 500px; height: 16px; background: var(--teal); }
  .band--dark { left: 508px; right: 0; height: 38px; background: var(--ink); }
</style>
</head>
<body>

  <section class="card card--front" aria-label="Card front">
    <div class="wordmark">
      <span class="wordmark__main">VOR</span>
      <span class="wordmark__sub">Exterior</span>
      <span class="wordmark__sub">Coatings</span>
    </div>
  </section>

  <section class="card card--back" aria-label="Card back">
    <div class="wordmark">
      <span class="wordmark__main">VOR</span>
      <span class="wordmark__sub">Exterior</span>
      <span class="wordmark__sub">Coatings</span>
    </div>

    <div class="divider"></div>

    <div class="contact">
      <p class="contact__name">MARCUS HALE</p>
      <p class="contact__title">Managing Director</p>

      <p class="contact__line">
        <svg viewBox="0 0 24 24" aria-hidden="true"><path fill="var(--teal)" d="M6.6 10.8a15.1 15.1 0 0 0 6.6 6.6l2.2-2.2a1 1 0 0 1 1-.25 11.4 11.4 0 0 0 3.6.57 1 1 0 0 1 1 1V20a1 1 0 0 1-1 1A17 17 0 0 1 3 4a1 1 0 0 1 1-1h3.5a1 1 0 0 1 1 1c0 1.25.2 2.45.57 3.57a1 1 0 0 1-.25 1z"/></svg>
        044-555 018 273
      </p>
      <p class="contact__line">
        <svg viewBox="0 0 24 24" aria-hidden="true"><rect x="2" y="5" width="20" height="14" rx="1" fill="var(--teal)"/><path d="M2.5 6 12 13l9.5-7" stroke="#fff" stroke-width="1.6" fill="none"/></svg>
        info@vorexterior.com
      </p>
      <p class="contact__line">
        <svg viewBox="0 0 24 24" aria-hidden="true"><circle cx="12" cy="12" r="10" fill="var(--teal)"/><g stroke="#fff" stroke-width="1.2" fill="none"><ellipse cx="12" cy="12" rx="4.2" ry="9.5"/><path d="M2.5 12h19M4 7h16M4 17h16M12 2.5v19"/></g></svg>
        www.vorexterior.com
      </p>

      <p class="contact__address">421, Address line here<br>Country Name, 45452</p>
    </div>

    <div class="band band--teal"></div>
    <div class="band band--dark"></div>
  </section>

</body>
</html>
```